Freelance business trainer needs a new business card

My business is called Brontlearn. I provide training in the workplace on management, coaching and mentoring, and customer service topics for a variety of businesses, colleges and private training providers, and teach on management programs. I need a professional but eye catching business card. Business colours grey and orange. My name Marion Tadwick; Tel 07382 415067; email mtadwick@brontlearn.co.uk; website www.brontlearn.co.uk.
Happy to have some sort of logo on front and details on back or all on one side
Target Market(s)
SME businesses and colleges - workshops i run are for adults in the workplace
Industry/Entity Type
Training
Look and feel

```html
<!DOCTYPE html>
<html lang="en">
<head>
<meta charset="utf-8">
<title>Brontlearn – Business Card</title>
<link rel="stylesheet" href="https://fonts.googleapis.com/css2?family=Roboto+Condensed:wght@400;700&display=swap">
<style>
  :root {
    --page: #e9e9ee;
    --card: #fafaf6;
    --grey: #6c6e70;
    --grey-light: #7b7d7f;
    --grey-text: #5a5c5e;
    --orange: #e07012;
    --white: #ffffff;
  }
  * { margin: 0; padding: 0; box-sizing: border-box; }
  html, body {
    width: 1200px;
    height: 800px;
    overflow: hidden;
    background: var(--page);
    font-family: "Roboto Condensed", "Arial Narrow", sans-serif;
  }
  .business-card {
    position: absolute;
    left: 120px;
    top: 120px;
    width: 960px;
    height: 560px;
    background: var(--card);
    overflow: hidden;
    box-shadow: 0 4px 14px rgba(0,0,0,0.12);
  }
  .feature-area {
    position: absolute;
    inset: 0;
    background: linear-gradient(to bottom, var(--grey-light), var(--grey));
    clip-path: polygon(480px 240px, 960px 240px, 960px 560px, 0 560px, 0 470px, 480px 470px);
  }
  .brand {
    position: absolute;
    left: 58px;
    top: 52px;
    display: flex;
    align-items: center;
    gap: 18px;
  }
  .brand-dot {
    width: 100px;
    height: 94px;
    border-radius: 50%;
    background: var(--orange);
  }
  .brand-name {
    font-size: 66px;
    font-weight: 400;
    color: var(--grey-text);
    letter-spacing: 0.5px;
  }
  .contact-list {
    position: absolute;
    left: 78px;
    top: 238px;
    list-style: none;
  }
  .contact-item {
    display: flex;
    align-items: center;
    gap: 14px;
    height: 36px;
    font-size: 25px;
    color: var(--grey-text);
    letter-spacing: 0.4px;
  }
  .contact-icon { width: 22px; height: 22px; flex: none; }
  .holder {
    position: absolute;
    right: 62px;
    top: 298px;
    text-align: right;
    color: var(--white);
  }
  .holder-name {
    font-size: 35px;
    font-weight: 700;
    letter-spacing: 0.3px;
  }
  .holder-role {
    margin-top: 8px;
    font-size: 25px;
    font-weight: 400;
    letter-spacing: 0.3px;
  }
</style>
</head>
<body>
  <div class="business-card">
    <div class="feature-area" role="img" aria-label="Grey and orange decorative wave artwork across the lower right of the card"></div>

    <div class="brand">
      <div class="brand-dot"></div>
      <span class="brand-name">Brontlearn</span>
    </div>

    <ul class="contact-list">
      <li class="contact-item">
        <svg class="contact-icon" viewBox="0 0 24 24" aria-hidden="true">
          <path fill="var(--orange)" d="M3,8 C3,5 6,4 12,4 C18,4 21,5 21,8 L21,10 L16,10 L16,8 L8,8 L8,10 L3,10 Z M7,11 L17,11 L20,20 L4,20 Z"/>
          <circle cx="12" cy="15.5" r="2.4" fill="var(--card)"/>
        </svg>
        <span>07382 415067</span>
      </li>
      <li class="contact-item">
        <svg class="contact-icon" viewBox="0 0 24 24" aria-hidden="true">
          <rect x="2" y="5" width="20" height="14" fill="var(--orange)"/>
          <path d="M2,5 L12,13 L22,5" fill="none" stroke="var(--card)" stroke-width="1.6"/>
        </svg>
        <span>mtadwick@brontlearn.co.uk</span>
      </li>
      <li class="contact-item">
        <svg class="contact-icon" viewBox="0 0 24 24" aria-hidden="true">
          <circle cx="12" cy="12" r="10" fill="var(--orange)"/>
          <g fill="none" stroke="var(--card)" stroke-width="1.2">
            <ellipse cx="12" cy="12" rx="4.5" ry="10"/>
            <line x1="2" y1="12" x2="22" y2="12"/>
            <line x1="12" y1="2" x2="12" y2="22"/>
            <path d="M4,7 L20,7 M4,17 L20,17"/>
          </g>
        </svg>
        <span>www.brontlearn.co.uk.</span>
      </li>
    </ul>

    <div class="holder">
      <div class="holder-name">Marion Tadwick</div>
      <div class="holder-role">Senior Education Consultant</div>
    </div>
  </div>
</body>
</html>
```